Property Services Company Needs a Brochure Design

Looking for a new brochure design for an existing property services company.

We provide a range of property services from, market research, real estate brokerage, valuation and appraisal, property development and other real estate consulting services.

We would like a fresh modern brochure design with good graphics and features. Our colours are white, blue and orange.

The design should communicate, attention to detail, superior service delivery and distinction in results.
Updates

I would like the brochure to be roughly about 20 pages.

Containing the following,

1) An introduction
2) Contents Page
2) What we do
3) Our Services
4) Agency & Brokerage
5) Real Estate Consulting
6) Market Research
7) Appraisal & Valuation
8) Project Management
9) Property Development

I would also like icons to represent items 4,5,6,7,8 & 9, they should be represented vertically on each of the pages from the contents page and highlighted individually on the pages that they represent.. i.e. on appraisal & valuation page, all six icons will be arranged vertically and the appraisal and valuations icon will be highlighted.

I will also like to have images that depict the services on the various pages.

I have some pages I think will flow which I will upload shortly.

Industry/Entity Type

Real Estate

Font styles to use
Serif

Colors
f78f20
0455a3

```html
<!DOCTYPE html>
<html lang="en">
<head>
<meta charset="utf-8">
<title>Market Research – Brochure Spread</title>
<link rel="stylesheet" href="https://fonts.googleapis.com/css2?family=Tinos&display=swap">
<style>
  :root {
    --bg: #e4e4e4;
    --paper: #f6f6f6;
    --purple: #4b3f7e;
    --orange: #e07a35;
    --ink-light: #ffffff;
    --photo-light: #ece9e3;
    --photo-mid: #cfc8bc;
    --photo-dark: #3a3f55;
  }
  * { box-sizing: border-box; margin: 0; padding: 0; }
  html, body { width: 1200px; height: 720px; overflow: hidden; }
  body {
    background: var(--bg);
    font-family: "Tinos", "Times New Roman", serif;
    position: relative;
  }
  .spread {
    position: absolute;
    left: 220px;
    top: 90px;
    width: 760px;
    height: 540px;
    display: flex;
    box-shadow: 0 18px 40px rgba(0,0,0,0.18);
  }
  .page {
    position: relative;
    width: 380px;
    height: 540px;
    background: var(--paper);
    overflow: hidden;
  }
  .page--left { border-right: 1px solid #dcdcdc; }
  .top-bar {
    position: absolute;
    top: 40px;
    height: 7px;
  }
  .top-bar--purple { background: var(--purple); }
  .top-bar--orange { background: var(--orange); }
  .photo-feature {
    position: absolute;
    left: 0;
    top: 52px;
    width: 540px;
    height: 360px;
    z-index: 1;
    background:
      radial-gradient(ellipse 130px 180px at 270px 200px, var(--photo-dark) 0%, rgba(58,63,85,0.85) 45%, rgba(58,63,85,0) 100%),
      linear-gradient(180deg, var(--photo-light) 0%, #f3efe8 55%, var(--photo-mid) 100%);
  }
  .section-title {
    position: absolute;
    right: 22px;
    top: 438px;
    color: var(--purple);
    font-size: 23px;
    letter-spacing: 0.5px;
    font-weight: 400;
  }
  .page-number {
    position: absolute;
    top: 484px;
    width: 26px;
    height: 26px;
    background: var(--purple);
    color: var(--ink-light);
    font-size: 11px;
    display: flex;
    align-items: center;
    justify-content: center;
  }
  .page--left .page-number { left: 26px; }
  .page--right .page-number { left: 326px; top: 472px; }
  .bottom-rule {
    position: absolute;
    left: 0; right: 0;
    top: 516px;
    height: 3px;
    background: var(--purple);
  }
  .bottom-band {
    position: absolute;
    left: 0; right: 0;
    top: 522px;
    height: 18px;
    background: var(--orange);
  }
  .building-art {
    position: absolute;
    left: 282px;
    top: 22px;
    width: 70px;
    height: 140px;
    background: linear-gradient(180deg, #d9d9d9, #c6c6c6);
  }
  .info-box {
    position: absolute;
    left: 164px;
    top: 238px;
    width: 182px;
    height: 228px;
    background: var(--orange);
    color: var(--ink-light);
    padding: 30px 20px 16px 26px;
    font-size: 9.2px;
    line-height: 1.22;
  }
  .info-box h3 {
    font-weight: 400;
    font-size: 9.5px;
    margin-bottom: 4px;
  }
</style>
</head>
<body>
  <div class="spread">
    <section class="page page--left">
      <div class="top-bar top-bar--purple" style="left:70px; width:126px;"></div>
      <div class="top-bar top-bar--orange" style="left:202px; width:178px; top:44px;"></div>
      <h2 class="section-title">MARKET RESEARCH</h2>
      <div class="page-number">11</div>
      <div class="bottom-rule"></div>
      <div class="bottom-band"></div>
    </section>
    <section class="page page--right">
      <div class="top-bar top-bar--orange" style="left:0; width:158px;"></div>
      <div class="top-bar top-bar--purple" style="left:164px; width:128px;"></div>
      <div class="building-art" role="img" aria-label="Line illustration of office towers"></div>
      <div class="info-box">
        <h3>Market Research</h3>
        <p>Our market research team, regularly conduct surveys across a wide range of areas in both the commercial and residential markets. They regularly produce market reports that can be used for a wide range of purposes. This information also provides our team members with superior knowledge of market trends, price shifts, occupancy rates and other unique trends. The information provided allows us to provide information useful for forecasting growth and trends in the market.</p>
      </div>
      <div class="page-number">12</div>
      <div class="bottom-rule"></div>
      <div class="bottom-band"></div>
    </section>
    <div class="photo-feature" role="img" aria-label="Photo of a smiling businessman in a suit reading a newspaper on a sofa in a bright office"></div>
  </div>
</body>
</html>
```